Vantro cards

I am in the auto motive, transportation business I would like a business card that is Something cool, modern edgy, having to do with car culture. I offer towing service for high and exotic cars. I also provide towing for collisions and car accidents. I offer open and enclosed transport nationwide.

Target Market(s)

Car culture people high end auto collectors

Industry/Entity Type

Towing car carrier

Contact Information for Business Card

My company colors black yellow and silver

Font styles to use
Serif

```html
<!DOCTYPE html>
<html lang="en">
<head>
<meta charset="utf-8">
<title>Vantro Business Cards</title>
<link rel="stylesheet" href="https://fonts.googleapis.com/css2?family=Roboto+Slab:wght@900&family=Poppins:wght@400;500&display=swap">
<style>
  :root {
    --backdrop: #2a2a2c;
    --card-black: #1c1c1e;
    --brand-yellow: #f7dc55;
    --yellow-deep: #d9b92a;
    --yellow-light: #fbe98a;
    --text-white: #ffffff;
    --rule-grey: #8a8a8a;
  }
  * { margin: 0; padding: 0; box-sizing: border-box; }
  html, body {
    width: 1200px;
    height: 1108px;
    overflow: hidden;
    background: var(--backdrop);
  }
  .card-pair {
    position: relative;
    width: 1200px;
    height: 1108px;
  }
  .card {
    position: absolute;
    top: 204px;
    width: 400px;
    height: 700px;
    border-radius: 22px;
    overflow: hidden;
  }
  .card-front {
    left: 170px;
    background: var(--card-black);
    color: var(--text-white);
    text-align: center;
    font-family: "Poppins", sans-serif;
  }
  .card-back { left: 630px; }

  .brand-block {
    margin-top: 120px;
    display: flex;
    align-items: center;
    justify-content: center;
    gap: 14px;
  }
  .brand-mark {
    width: 26px;
    height: 26px;
    background: var(--brand-yellow);
  }
  .brand-name {
    font-family: "Roboto Slab", serif;
    font-weight: 900;
    font-size: 64px;
    letter-spacing: 2px;
    color: var(--brand-yellow);
    line-height: 1;
  }

  .person-name {
    margin-top: 150px;
    font-family: "Roboto Slab", serif;
    font-weight: 900;
    font-size: 30px;
    letter-spacing: 1px;
    color: var(--brand-yellow);
    text-transform: uppercase;
  }
  .person-role {
    margin-top: 2px;
    font-size: 17px;
    letter-spacing: 1px;
    text-transform: uppercase;
  }

  .icon-row {
    margin: 20px auto 0;
    width: 300px;
    display: flex;
    align-items: center;
    gap: 8px;
  }
  .icon-row .rule { flex: 1; height: 1px; background: var(--rule-grey); }
  .contact-icon {
    width: 28px;
    height: 28px;
    border-radius: 5px;
    background: var(--brand-yellow);
    display: flex;
    align-items: center;
    justify-content: center;
  }
  .contact-icon svg { width: 18px; height: 18px; }

  .contact-list {
    margin-top: 10px;
    list-style: none;
    font-size: 19px;
    line-height: 1.35;
  }
  .divider {
    margin: 14px auto;
    width: 300px;
    height: 1px;
    background: var(--rule-grey);
  }
  .address {
    font-size: 19px;
    line-height: 1.35;
    font-style: normal;
  }

  .truck-pattern {
    width: 100%;
    height: 100%;
    background: linear-gradient(135deg, var(--yellow-light) 0%, var(--brand-yellow) 45%, var(--yellow-deep) 100%);
  }
</style>
</head>
<body>
  <main class="card-pair">
    <section class="card card-front">
      <div class="brand-block">
        <span class="brand-mark"></span>
        <span class="brand-name">VANTRO</span>
      </div>

      <h1 class="person-name">Marcus Hale</h1>
      <p class="person-role">Managing Director</p>

      <div class="icon-row">
        <span class="rule"></span>
        <span class="contact-icon">
          <svg viewBox="0 0 24 24" aria-hidden="true"><path fill="#1c1c1e" d="M6.6 10.8a15 15 0 0 0 6.6 6.6l2.2-2.2a1 1 0 0 1 1-.25 11.4 11.4 0 0 0 3.6.57 1 1 0 0 1 1 1V20a1 1 0 0 1-1 1A17 17 0 0 1 3 4a1 1 0 0 1 1-1h3.5a1 1 0 0 1 1 1c0 1.25.2 2.45.57 3.57a1 1 0 0 1-.25 1z"/></svg>
        </span>
        <span class="contact-icon">
          <svg viewBox="0 0 24 24" aria-hidden="true"><rect x="3" y="5" width="18" height="14" rx="1" fill="none" stroke="#1c1c1e" stroke-width="2"/><path d="M3 6l9 7 9-7" fill="none" stroke="#1c1c1e" stroke-width="2"/></svg>
        </span>
        <span class="contact-icon">
          <svg viewBox="0 0 24 24" aria-hidden="true"><circle cx="12" cy="12" r="9" fill="none" stroke="#1c1c1e" stroke-width="2"/><path d="M3 12h18M12 3c3 3 3 15 0 18M12 3c-3 3-3 15 0 18" fill="none" stroke="#1c1c1e" stroke-width="1.6"/></svg>
        </span>
        <span class="rule"></span>
      </div>

      <ul class="contact-list">
        <li>044-987 654 321</li>
        <li>info@vantrotow.com</li>
        <li>www.vantrotow.com</li>
      </ul>

      <div class="divider"></div>

      <address class="address">
        88, Harbor Road, Suite 4<br>
        30211,United States
      </address>
    </section>

    <section class="card card-back">
      <div class="truck-pattern" role="img" aria-label="Repeating embossed pattern of flatbed tow trucks on glossy yellow"></div>
    </section>
  </main>
</body>
</html>
```